Förderverein einer Kirchengemeinde sucht Flyer-Design
Zielgruppe
Wir sind ein Förderverein einer Kirchengemeinde, der sich für die kirchenmusikalische Arbeit einsetzt.
Wir wünschen uns ein niveauvolles und zeitgemäßes/modernes Flyerdesign, das die etablierten Konzertbesucher anspricht, aber vor allem auch Menschen erreicht und überzeugt, die (noch) nichts mit Kirche zu tun haben.
Das Alter der (Haupt-) Zielgruppe (Männer und Frauen) erstreckt sich von 45 bis 70 Jahren.
Aufgabenstellung
Bei der Wahl des Formates würden wir (aus der Sicht von Laien) ein zweimal gefaltetes DIN A4 quer Format nehmen. Aber wir lassen uns gerne überraschen und sind grundsätzlich für andere Lösungen offen.
Bitte den Abschnitt für Adress- und sonstige Dateneintragungen samt Kontodaten so gestalten und platzieren, dass man ihn leicht abtrennen und verschicken kann.
Der Flyer soll Kirchenmusik als lebendig und attraktiv darstellen und neue (jüngere) Mitglieder für den Freundeskreis werben.
Lassen Sie die Bilder sprechen!!

```html
<!DOCTYPE html>
<html lang="de">
<head>
<meta charset="utf-8">
<title>Freundeskreis Kirchenmusik – Flyer</title>
<link rel="stylesheet" href="https://fonts.googleapis.com/css2?family=Crimson+Pro:wght@500;700&family=Source+Sans+3:wght@400;600&family=Allura&display=swap">
<style>
  :root{
    --blue:#566c95;
    --blue-deep:#4b6089;
    --ink:#ffffff;
    --ink-soft:#e4e9f3;
    --field-top:#eef0f5;
    --field-bottom:#d9dde8;
    --fold:rgba(255,255,255,.35);
    --page:#ffffff;
  }
  *{box-sizing:border-box;margin:0;padding:0}
  html,body{width:820px;height:1200px;overflow:hidden;background:var(--page)}
  body{position:relative;font-family:"Source Sans 3",Arial,sans-serif;color:var(--ink)}
  .sheet{position:absolute;left:31px;width:758px;background:var(--blue);box-shadow:0 2px 6px rgba(0,0,0,.18)}
  .sheet--outside{top:22px;height:552px}
  .sheet--inside{top:618px;height:562px}
  .panel{position:absolute;top:0;width:253px;height:100%}
  .panel--1{left:0}.panel--2{left:253px}.panel--3{left:506px}
  .fold{position:absolute;top:0;bottom:0;width:0;border-left:1px dashed var(--fold)}
  .fold--soft{border-left:1px solid rgba(0,0,0,.08)}
  .photo{position:absolute;border-radius:50%;overflow:hidden}
  .heading{font-family:"Crimson Pro",Georgia,serif;font-weight:700;font-size:15px;line-height:1.2;letter-spacing:.2px}
  .copy{font-size:9.5px;line-height:1.3;color:var(--ink-soft)}
  .copy p+p{margin-top:9px}
  .script{position:absolute;font-family:"Allura",cursive;font-size:30px;line-height:.95;color:var(--ink);text-align:center;white-space:nowrap}
  .field{height:25px;background:linear-gradient(90deg,var(--field-top),var(--field-bottom))}
  .field-label{font-size:7px;line-height:9px;height:9px;color:var(--ink-soft);margin:2px 0 6px}
  .form{position:absolute;left:25px;width:202px}
  .form--join{left:19px;width:210px}
  .form--join .field{height:23px}
  .form--join .field-label{margin:2px 0 4px}
  .reasons{list-style:none}
  .reasons li{margin-bottom:14px}
  .reasons--tight li{margin-bottom:11px}
  .fees{list-style:none;font-size:9.5px;color:var(--ink-soft)}
  .fees li{display:flex;align-items:center;gap:10px;height:19px}
  .fees .dot{width:11px;height:11px;border-radius:50%;background:var(--field-top);flex:none}
  .amount{display:inline-block;width:110px;height:16px;background:linear-gradient(90deg,var(--field-top),var(--field-bottom));vertical-align:middle}
  .brand{position:absolute;left:0;right:0;top:48px;text-align:center}
  .brand-mark{width:34px;height:34px;background:var(--ink);margin:0 auto 56px}
  .brand-name{font-family:"Crimson Pro",Georgia,serif;font-weight:500;font-size:33px;line-height:1.05}
  a{color:inherit}
</style>
</head>
<body>

<section class="sheet sheet--outside">
  <div class="fold" style="left:253px"></div>
  <div class="fold fold--soft" style="left:506px"></div>

  <div class="panel panel--1">
    <div class="photo" role="img" aria-label="Foto: Registerzüge einer Orgel in Nahaufnahme"
         style="left:14px;top:-12px;width:196px;height:128px;border-radius:48% 52% 50% 50%/40% 40% 60% 60%;background:linear-gradient(135deg,#c59a5a,#6d4326 55%,#c9b89c)"></div>
    <h2 class="heading" style="position:absolute;left:25px;top:172px">SEPA-Lastschriftmandat</h2>
    <div class="form" style="top:197px">
      <div class="field"></div><div class="field-label">IBAN</div>
      <div class="field"></div><div class="field-label">BIC</div>
      <div class="field"></div><div class="field-label">Kreditinstitut</div>
      <div class="field"></div><div class="field-label">Kontoinhaber</div>
    </div>
    <p class="copy" style="position:absolute;left:25px;top:384px;width:210px">Hiermit ermächtige ich den Freundeskreis Kirchenmusik den von mir zu entrichtenden Mitgliedsbeitrag von meinem Konto einzuziehen.</p>
    <div class="form" style="top:433px">
      <div class="field"></div>
      <div class="field-label">Ort, Datum&nbsp;&nbsp;&nbsp;&nbsp;&nbsp;&nbsp;&nbsp;&nbsp;&nbsp;&nbsp;&nbsp;&nbsp;&nbsp;&nbsp;Unterschrift</div>
    </div>
    <p class="copy" style="position:absolute;left:25px;top:490px;width:210px">Der Einzug der Mitgliedsbeiträge erfolgt zu Beginn eines Kalenderjahres.</p>
  </div>

  <div class="panel panel--2">
    <div style="position:absolute;left:29px;top:24px;width:205px">
      <h2 class="heading">Spendenkonto</h2>
      <p class="copy" style="margin-top:12px">Sparkasse Lindenau-Hohenfeld<br>IBAN: DE00123456780000004711<br>BIC: NOLADE00LND</p>
      <p class="copy" style="margin-top:9px">Verwendungszweck bei Einzelspenden unter Angabe der Kostenstelle.</p>
    </div>
    <div class="photo" role="img" aria-label="Foto: Hände spielen Trompete"
         style="left:10px;top:147px;width:185px;height:106px;background:linear-gradient(120deg,#d9b98c,#c69a3c 45%,#8d6b4a)"></div>
    <div class="photo" role="img" aria-label="Foto: historischer Orgelprospekt"
         style="left:68px;top:245px;width:165px;height:108px;background:linear-gradient(180deg,#d7cdbb,#9b8f7f 50%,#5d5448)"></div>
    <div class="copy" style="position:absolute;left:29px;top:362px;width:200px">
      <p>Wenn Sie die Kirchenmusik an St. Aurelius als Mitglied im Freundeskreis Kirchenmusik fördern möchten, senden Sie das ausgefüllte Formular auf der Rückseite an den</p>
      <p>Freundeskreis Kirchenmusik<br>Kirchengemeinde St. Aurelius<br>Marktgasse 7, 12345 Lindenau</p>
      <p>Tel.: 01234-56 78 90, anna.berger@kirchenpost.de</p>
      <p>Nähere Informationen zur Kirchenmusik an St. Aurelius und zum Freundeskreis finden Sie unter <a href="#">www.kirchenmusik-lindenau.de</a></p>
    </div>
  </div>

  <div class="panel panel--3">
    <div class="brand">
      <div class="brand-mark"></div>
      <div class="brand-name">Freundeskreis<br>Kirchenmusik</div>
    </div>
    <div role="img" aria-label="Dekor: großer Notenschlüssel"
         style="position:absolute;left:20px;top:300px;width:66px;height:168px;border-radius:40px;background:var(--blue-deep)"></div>
    <div class="script" style="left:58px;top:318px;transform:rotate(-10deg)">Kirchenmusik<br>braucht<br>Freunde</div>
  </div>
</section>

<section class="sheet sheet--inside">
  <div class="fold fold--soft" style="left:253px"></div>
  <div class="fold" style="left:506px"></div>

  <div class="panel panel--1">
    <div class="photo" role="img" aria-label="Foto: Posaunenchor mit Blechblasinstrumenten vor einem Gebäude"
         style="left:10px;top:20px;width:188px;height:130px;background:linear-gradient(180deg,#e8e6e0,#b7b3aa 55%,#6f6a60)"></div>
    <div class="photo" role="img" aria-label="Foto: Flötenensemble als Gruppe"
         style="left:120px;top:108px;width:160px;height:120px;background:linear-gradient(180deg,#9aa58a,#cfc7b8 55%,#6a6b63)"></div>
    <div class="script" style="left:14px;top:176px;font-size:27px;transform:rotate(-12deg)">Mitglieder haben<br>gute Gründe</div>
    <div class="copy" style="position:absolute;left:36px;top:256px;width:195px">
      <p style="margin-bottom:14px">Sie…</p>
      <ul class="reasons">
        <li>…erhalten ermäßigte Eintrittspreise von gemeindeeigenen Konzerten</li>
        <li>…können Konzertkarten vor dem öffentlichen Verkauf erwerben</li>
        <li>…gestalten die Arbeit des Freundes­kreises in der jährlichen Mitglieder­versammlungen aktiv mit</li>
        <li>…erhalten aktuelle Informationen über Veranstaltungen der Gemeinde bequem per Email und profitieren so zu allererst</li>
        <li>…können den Mitgliedsbeitrag steuerlich absetzen und erhalten eine Spendenbescheinigung</li>
        <li>…können an Ausflügen des Freundeskreises teilnehmen</li>
      </ul>
    </div>
  </div>

  <div class="panel panel--2">
    <div class="script" style="left:22px;top:30px;font-size:27px;transform:rotate(-9deg)">Kirchenmusik<br>braucht Freunde</div>
    <div class="photo" role="img" aria-label="Foto: Chor und Orchester im barocken Kirchenraum"
         style="left:57px;top:76px;width:170px;height:120px;background:linear-gradient(180deg,#d9c9b6,#b89378 45%,#3d3230)"></div>
    <div class="copy" style="position:absolute;left:44px;top:206px;width:192px">
      <p>Im Jahr 1999 gegründet, unterstützt der Freundeskreis Kirchenmusik die vielfältigen musikalischen Aktivitäten an der St. Aurelius-Kirche.</p>
      <p style="margin-top:11px">Wir laden Sie ein, Mitglied zu werden!</p>
      <p style="margin-top:11px">Mit Ihrem Beitrag …</p>
      <ul class="reasons reasons--tight" style="margin-top:9px">
        <li>…bereichern Sie Lindenaus kulturelle Landschaft durch den Erhalt und Ausbau unseres hohen kirchenmusikalischen Niveaus</li>
        <li>…stärken Sie das Ehrenamt</li>
        <li>…ermöglichen Sie der Kantorei, dem Posaunenchor, dem Kinderchor und dem Flötenensemble regelmäßige Probenarbeit, Probenwochenenden und die Anschaffung von Notenmaterial</li>
        <li>…erhalten Sie die historische Johann Meister Orgel von 1748</li>
        <li style="margin-bottom:0">…fördern Sie die Ausbildung kirchenmusikalischen Nachwuchses</li>
      </ul>
    </div>
  </div>

  <div class="panel panel--3">
    <h2 class="heading" style="position:absolute;left:19px;top:18px">Beitrittserklärung</h2>
    <div class="form form--join" style="top:42px">
      <div class="field"></div><div class="field-label">Name, Vorname</div>
      <div class="field"></div><div class="field-label">für die Institution/Firma + persönlich</div>
      <div class="field"></div><div class="field-label">Straße, Hausnr.</div>
      <div class="field"></div><div class="field-label">PLZ, Ort</div>
      <div class="field"></div><div class="field-label">Telefon/Handy</div>
      <div class="field"></div><div class="field-label">Emailadresse</div>
      <div class="field"></div><div class="field-label">Geburtstag</div>
      <div class="field"></div><div class="field-label">Datum, Unterschrift</div>
    </div>
    <h2 class="heading" style="position:absolute;left:19px;top:362px">Mitgliedsbeiträge</h2>
    <ul class="fees" style="position:absolute;left:19px;top:392px;width:220px">
      <li><span class="dot"></span>jeweils Mindestbeiträge</li>
      <li><span class="dot"></span>Einzelpersonen 20 €</li>
      <li><span class="dot"></span>Ehepaare/Partnerschaften 32€</li>
      <li><span class="dot"></span>Institutionen/Firmen 95 €</li>
      <li style="height:28px;align-items:flex-start"><span class="dot" style="margin-top:3px"></span><span style="line-height:1.1"><span class="amount"></span> €<br><span style="font-size:6.5px">Bitte frei wählbaren Betrag einfügen</span></span></li>
      <li><span class="dot"></span>ich benötige eine Spendenbescheinigung</li>
      <li><span class="dot"></span>Einmalige Spende (ohne Mitgliedschaft)</li>
    </ul>
  </div>
</section>

</body>
</html>
```